Business Card Design

New business card design

Target Market(s)

Residential & Commercial Property Managers

Industry/Entity Type

Plumbing Services

Contact Information for Business Card

Name - Rowan Keddle, title - Director, Phone Number - 0431 286 517, email - rowan@tbk-plumbing.com.au, Company ABN - 73 215 904 386,

Font styles to use
Sans Serif

Colors
0054AA
0677BA
7BADD7
CADEEF
E8F1F8

```html
<!DOCTYPE html>
<html lang="en">
<head>
<meta charset="utf-8">
<title>TBK Plumbing Services – Business Card</title>
<link rel="stylesheet" href="https://fonts.googleapis.com/css2?family=Montserrat:wght@400;500;700&display=swap">
<style>
  :root {
    --backdrop: #161b20;
    --card-white: #ffffff;
    --navy: #1e252c;
    --brand-blue: #2aa7e1;
    --ink: #1d2329;
  }
  html, body {
    margin: 0;
    width: 1200px;
    height: 900px;
    overflow: hidden;
    background: var(--backdrop);
    font-family: "Montserrat", Arial, sans-serif;
  }
  .card {
    position: absolute;
    left: 150px;
    top: 175px;
    width: 900px;
    height: 550px;
    border-radius: 34px;
    background: var(--card-white);
    overflow: hidden;
    box-shadow: 0 20px 50px rgba(0,0,0,.5);
  }
  .card__wave {
    position: absolute;
    inset: 0;
  }
  .brand {
    position: absolute;
    left: 70px;
    top: 205px;
    display: flex;
    align-items: center;
    gap: 14px;
  }
  .brand__dot {
    width: 26px;
    height: 26px;
    border-radius: 50%;
    background: var(--brand-blue);
  }
  .brand__name {
    font-weight: 500;
    font-size: 26px;
    letter-spacing: 1px;
    color: var(--ink);
    line-height: 1.25;
  }
  .divider {
    position: absolute;
    left: 420px;
    top: 170px;
    width: 2px;
    height: 210px;
    background: var(--brand-blue);
  }
  .contact {
    position: absolute;
    left: 455px;
    top: 165px;
    color: var(--ink);
  }
  .contact__name {
    margin: 0;
    font-weight: 700;
    font-size: 36px;
    color: var(--brand-blue);
    line-height: 1.1;
  }
  .contact__title {
    margin: 2px 0 18px;
    font-size: 23px;
    font-weight: 500;
  }
  .contact__line {
    display: flex;
    align-items: center;
    gap: 10px;
    margin: 0 0 10px;
    font-size: 23px;
    font-weight: 500;
  }
  .contact__label { color: var(--brand-blue); font-weight: 400; }
  .contact__icon { width: 20px; height: 20px; flex: none; }
</style>
</head>
<body>
  <div class="card">
    <svg class="card__wave" viewBox="0 0 900 550" width="900" height="550" aria-hidden="true">
      <path d="M0,455 C140,520 360,468 580,500 C720,520 810,535 860,550 L0,550 Z" fill="var(--navy)"/>
      <path d="M0,455 C140,520 360,468 580,500 C720,520 810,535 860,550 L880,550 C820,528 730,505 580,490 C360,462 140,508 0,448 Z" fill="var(--brand-blue)"/>
    </svg>

    <div class="brand">
      <span class="brand__dot"></span>
      <span class="brand__name">TBK<br>Plumbing Services</span>
    </div>

    <div class="divider"></div>

    <div class="contact">
      <h1 class="contact__name">Rowan Keddle</h1>
      <p class="contact__title">Director</p>
      <p class="contact__line"><span class="contact__label">ABN</span> - 73 215 904 386</p>
      <p class="contact__line">
        <svg class="contact__icon" viewBox="0 0 24 24"><path fill="var(--brand-blue)" d="M6.6 10.8a15.2 15.2 0 0 0 6.6 6.6l2.2-2.2c.3-.3.7-.4 1-.2 1.1.4 2.3.6 3.6.6.6 0 1 .4 1 1V20c0 .6-.4 1-1 1A17 17 0 0 1 3 4c0-.6.4-1 1-1h3.5c.6 0 1 .4 1 1 0 1.3.2 2.5.6 3.6.1.3 0 .7-.2 1z"/></svg>
        0431 286 517
      </p>
      <p class="contact__line">
        <svg class="contact__icon" viewBox="0 0 24 24"><rect x="2" y="5" width="20" height="14" rx="1.5" fill="var(--brand-blue)"/><path d="M3 6l9 7 9-7" fill="none" stroke="#fff" stroke-width="1.6"/></svg>
        rowan@tbk-plumbing.com.au
      </p>
    </div>
  </div>
</body>
</html>
```